I need a website designed for my hair extensions business

I have some before and afters you can use

https://example-photos.net/p/Qm4trLwKoBa/

https://www.example-photos.net/p/Hvno7PaWkeR/?sid=QtPwZjN0cVhkYmRxUb==
Hi I offer tiny weave hair extensions
My instagram page is Virelahairextensionsstudio

I’m needing a Lux website
I have been doing weave hair extensions for 16 years and I specialise in only the finest installation and hair quality

The website must attract a high profile cliental

I have thousands of photos on my instagram page you can use

The website must be coded to attract hair extensions clients from all over Victoria Australia
It must have what’s relevant for google to recognise the website to Potential clients

recognise

Some are the below
Apologies for the confusion. Here are some SEO keywords that can be used for a website focused on Weave Hair Extensions in Victoria, Australia:

1. Weave hair extensions Victoria
2. Best weave hair extensions Australia
3. Affordable weave hair extensions
4. Professional weave hair extensions
5. High-quality weave hair extensions
6. Victoria weave hair extension services
7. Top-rated weave hair extension salon
8. Natural-looking weave hair extensions
9. Customizable weave hair extensions
10. Victoria's premier weave hair extensions

Remember to incorporate these keywords strategically into your website's content, including titles, headings, meta descriptions, and throughout the body text. This will help improve your website's visibility in search engine results and attract relevant traffic from individuals looking for weave hair extensions in Victoria, Australia.

Please make the website look elegant not tacky no pink or script writing please

Target Market(s)

Woman between 21 to 60

Industry/Entity Type

https://www.example-photos.net/reel/KpwwoTYBv7M/?sid=QtPwZjN0cVhkYmRxUb==

Coding

Coded - Design and coding required

Number of Pages Required

3 page

Requirements
Must have
• Description of myself 16 years experience, I’ve installed 1000s of weave hair extensions, my intention to deal is guaranteed.
Nice to have
• I have added 2 images or how flat and tiny the weave hair extensions are, here is a link to a video that can be used https://www.example-photos.net/reel/KpwwoTYBv7M/?sid=QtPwZjN0cVhkYmRxUb== The website should look elegant, the extensions I install are spectacular. You can see the before and after on my instagram page virela hair extensions studio. The pictures of my work should be taken from my instagram page as I own those photos
Should not have
• My website should not have pink or script writing it needs to attract a high cliental the website must look elegant

```html
<!DOCTYPE html>
<html lang="en">
<head>
<meta charset="utf-8">
<title>Virela Hair Extensions — Weave Hair Extensions Victoria</title>
<link href="https://fonts.googleapis.com/css2?family=Cormorant+Garamond:wght@500;600&family=Manrope:wght@400;500;600&display=swap" rel="stylesheet">
<style>
:root{
  --page:#ffffff;
  --header:#faf7f4;
  --blush:#f1ebe6;
  --wave:#cdb9a6;
  --panel:#f6f1ec;
  --accent:#8a6a4f;
  --accent-soft:#a88b6e;
  --button:#cbb092;
  --ink:#2b2b2b;
  --ink-soft:#3d3d3d;
  --button-ink:#2a211b;
}
*{margin:0;padding:0;box-sizing:border-box}
html,body{width:1200px;height:3982px;overflow:hidden;background:var(--page)}
body{position:relative;font-family:'Manrope',sans-serif;color:var(--ink)}
.abs{position:absolute}
.header{left:0;top:0;width:1200px;height:85px;background:var(--header)}
.logo{font-family:'Cormorant Garamond',serif;font-weight:600;color:var(--accent);font-size:36px;white-space:nowrap;letter-spacing:.5px}
.nav a{position:absolute;font-size:15px;font-weight:500;color:var(--ink);text-decoration:none;transform:translateX(-50%);white-space:nowrap}
.hero-bg{left:0;top:85px;width:1200px;height:560px}
.hero-text{right:698px;top:160px;width:420px;text-align:right}
.hero-text .kicker{font-family:'Cormorant Garamond',serif;font-size:30px;color:var(--accent-soft);font-weight:600}
.hero-text h1{font-family:'Cormorant Garamond',serif;font-size:42px;color:var(--accent);font-weight:600;line-height:1.3}
.hero-text p{font-size:16px;line-height:30px;color:var(--ink-soft);margin-top:22px}
.btn{position:absolute;z-index:3;background:var(--button);border-radius:26px;font-family:'Cormorant Garamond',serif;font-weight:600;color:var(--button-ink);font-size:26px;display:flex;align-items:center;justify-content:center;text-decoration:none}
.photo{position:absolute}
.section-title{position:absolute;left:0;width:1200px;text-align:center;font-family:'Cormorant Garamond',serif;font-weight:600;color:var(--accent);font-size:42px}
.panel{position:absolute;background:var(--panel)}
.body-copy{font-size:16px;line-height:34px;color:var(--ink-soft)}
.tile{position:absolute;top:1467px;width:233px;height:316px;border-radius:10px;overflow:hidden}
.tile-label{position:absolute;left:0;width:100%;text-align:center;font-family:'Cormorant Garamond',serif;font-weight:600;color:#fff;font-size:32px;top:100px}
.price{position:absolute;left:69px;top:174px;width:95px;height:36px;border-radius:18px;background:var(--button);color:#fff;font-size:19px;display:flex;align-items:center;justify-content:center}
.ba-label{position:absolute;top:2328px;width:166px;height:53px;background:var(--button);display:flex;align-items:center;justify-content:center;font-family:'Cormorant Garamond',serif;font-weight:600;font-size:28px;color:var(--button-ink)}
.faq-item{position:absolute;left:284px;width:632px;height:62px;background:#fff;border-radius:8px;box-shadow:0 2px 10px rgba(0,0,0,.09);display:flex;align-items:center;padding:0 22px;font-size:17.5px;color:var(--ink-soft)}
.faq-item .plus{position:absolute;right:22px;top:22px;width:18px;height:18px;border-radius:50%;background:var(--accent-soft)}
.faq-item .plus::before,.faq-item .plus::after{content:"";position:absolute;background:#fff;left:4px;top:8px;width:10px;height:2px}
.faq-item .plus::after{transform:rotate(90deg)}
.footer-nav a{position:absolute;top:3810px;transform:translateX(-50%);font-size:15px;font-weight:500;color:var(--ink);text-decoration:none;white-space:nowrap}
.social{position:absolute;top:3855px;width:44px;height:44px;border-radius:50%;border:2px solid #555;background:#fff}
.copyright{left:0;top:3921px;width:1200px;text-align:center;font-size:14px;font-weight:500;color:var(--ink)}
</style>
</head>
<body>

<header class="abs header">
  <div class="abs logo" style="left:110px;top:22px">Virela Hair Extensions</div>
  <nav class="nav">
    <a href="#" style="left:567px;top:38px">HOME</a>
    <a href="#" style="left:676px;top:38px">ABOUT ME</a>
    <a href="#" style="left:776px;top:38px">FAQ</a>
    <a href="#" style="left:875px;top:38px">CONTACT</a>
  </nav>
  <svg class="abs" style="left:1062px;top:31px" width="26" height="26" viewBox="0 0 26 26" aria-label="Search">
    <circle cx="10.5" cy="10.5" r="7.5" fill="none" stroke="#a88b6e" stroke-width="3"/>
    <line x1="16" y1="16" x2="23" y2="23" stroke="#a88b6e" stroke-width="3.5" stroke-linecap="round"/>
  </svg>
</header>

<svg class="abs hero-bg" width="1200" height="560" viewBox="0 0 1200 560">
  <path d="M0 0H1200V520C1080 535 990 555 860 540C700 520 560 470 380 540C240 590 120 545 0 520Z" fill="var(--blush)"/>
  <path d="M0 517C120 542 240 585 380 535C560 468 700 518 860 537C990 552 1080 532 1200 517V525C1080 540 990 560 860 545C700 526 560 476 380 545C240 595 120 550 0 525Z" fill="var(--wave)"/>
</svg>

<div class="abs hero-text">
  <div class="kicker">Welcome To</div>
  <h1>Virela Hair Extensions</h1>
  <p>Sed ut perspiciatis unde omnis iste natus error sit voluptatem accusantium doloremque laudantium, totam rem aperiam, eaque ipsa quae</p>
</div>
<a class="btn" href="#" style="left:322px;top:397px;width:181px;height:51px">Get Started</a>

<div class="photo" role="img" aria-label="Woman with long straight dark hair in a gold satin dress" style="left:795px;top:108px;width:285px;height:510px;border-radius:140px 140px 0 0;background:linear-gradient(180deg,#3a2a26 0%,#b58a6e 40%,#c9ad68 75%,#a48b48 100%)"></div>
<div class="photo" role="img" aria-label="Hair fiber applicator" style="left:372px;top:487px;width:138px;height:200px;border-radius:60px 60px 20px 20px;background:linear-gradient(160deg,#2f2f2f 0%,#1f1f1f 70%,#8a8a8a 100%)"></div>
<div class="photo" role="img" aria-label="Hair building fiber bottles and hairline comb" style="left:514px;top:382px;width:326px;height:322px;border-radius:30px;background:linear-gradient(90deg,#2b2b2b 0%,#3a3a3a 30%,#e9e9e9 45%,#d8d8d8 60%,#2f2f2f 75%,#1f1f1f 100%)"></div>

<h2 class="section-title" style="top:758px">About Me</h2>
<div class="panel" style="left:464px;top:873px;width:612px;height:392px"></div>
<div class="photo" style="left:124px;top:852px;width:340px;height:424px;border-radius:26px 26px 10px 26px;background:var(--accent-soft)"></div>
<div class="photo" role="img" aria-label="Portrait of the stylist with long blonde wavy hair" style="left:124px;top:852px;width:333px;height:417px;border-radius:26px 26px 10px 0;background:linear-gradient(180deg,#8f8477 0%,#d9bf95 35%,#c9ab80 60%,#2a2a2a 100%)"></div>
<div class="abs body-copy" style="left:507px;top:920px;width:525px">
  <p>16 years experience, I've installed 1000s of weave hair extensions, my intention to deal is guaranteed.</p>
  <p style="margin-top:6px;text-align:justify">Lorem ipsum dolor sit amet, consectetur adipiscing elit, sed do eiusmod tempor incididunt ut labore et dolore magna aliqua. Ut enim ad minim veniam, quis nostrud exercitation ullamco laboris nisi ut aliquip ex ea commodo consequat. Duis aute irure dolor in</p>
</div>
<a class="btn" href="#" style="left:507px;top:1155px;width:181px;height:51px">Learn More</a>

<h2 class="section-title" style="top:1360px">Top-rated weave hair extension salon</h2>
<div class="tile" role="img" aria-label="Row of fiber bottles in assorted hair shades" style="left:120px;background:linear-gradient(135deg,#2d2d2d 0%,#4a4a4a 45%,#8a6a50 75%,#f2ede4 100%)"></div>
<div class="tile" role="img" aria-label="Bundle of brown hair extensions on a red glitter heart" style="left:361px;background:linear-gradient(160deg,#6e5a4c 0%,#8e2a24 40%,#5a4a40 70%,#8d8278 100%)">
  <div class="tile-label">Lorem ipsum</div>
  <div class="price">$32.8</div>
</div>
<div class="tile" role="img" aria-label="Fiber spray and bottle through torn paper" style="left:602px;background:radial-gradient(ellipse at 50% 55%,#1b1b1b 0%,#1b1b1b 38%,#e9d3cf 60%,#f3e6e2 100%)"></div>
<div class="tile" role="img" aria-label="Shelves stocked with hair care product boxes" style="left:843px;background:linear-gradient(180deg,#d9d9d9 0%,#7a7a7a 50%,#efefef 80%,#3a3a3a 100%)"></div>
<a class="btn" href="#" style="left:489px;top:1840px;width:196px;height:51px">View Products</a>

<div class="photo" role="img" aria-label="Before: head with short hair and clipped weave rows" style="left:332px;top:1984px;width:268px;height:374px;border-radius:20px 0 0 20px;background:linear-gradient(180deg,#c9c3c3 0%,#6b4a3a 35%,#a78366 65%,#e9ddd0 100%)"></div>
<div class="photo" role="img" aria-label="After: long straight blonde weave hair extensions" style="left:602px;top:1984px;width:267px;height:374px;border-radius:0 20px 20px 0;background:linear-gradient(180deg,#9c9592 0%,#d8c39a 35%,#e7d6b3 65%,#3b3b3b 100%)"></div>
<div class="abs" style="left:599px;top:1984px;width:3px;height:400px;background:#fff"></div>
<svg class="abs" style="left:574px;top:2144px" width="54" height="54" viewBox="0 0 54 54" aria-label="Slide to compare">
  <circle cx="27" cy="27" r="26" fill="#fff"/>
  <path d="M23 19L15 27L23 35M31 19L39 27L31 35" fill="none" stroke="#222" stroke-width="2.8" stroke-linecap="round" stroke-linejoin="round"/>
</svg>
<div class="ba-label" style="left:383px">Before</div>
<div class="ba-label" style="left:640px">After</div>

<div class="panel" style="left:134px;top:2497px;width:593px;height:390px"></div>
<div class="abs body-copy" style="left:173px;top:2545px;width:525px;text-align:justify">Lorem ipsum dolor sit amet, consectetur adipiscing elit, sed do eiusmod tempor incididunt ut labore et dolore magna aliqua. Ut enim ad minim veniam, quis nostrud exercitation ullamco laboris nisi ut aliquip ex ea commodo consequat. Duis aute irure dolor in reprehenderit in voluptate velit esse cillum dolore eu fugiat nulla pariatur. Excepteur sint occaecat cupidatat non proident, sunt in</div>
<a class="btn" href="#" style="left:515px;top:2780px;width:181px;height:51px">Read More</a>
<div class="photo" style="left:727px;top:2477px;width:340px;height:424px;border-radius:22px 22px 22px 10px;background:var(--accent-soft)"></div>
<div class="photo" role="img" aria-label="Video still: close-up of a flat tiny weave row in dark hair" style="left:734px;top:2477px;width:333px;height:417px;border-radius:22px 22px 22px 0;background:linear-gradient(180deg,#3a2a24 0%,#5e4a42 30%,#cfc4c2 45%,#6b4a38 60%,#2a1d18 100%)"></div>
<svg class="abs" style="left:883px;top:2674px" width="36" height="24" viewBox="0 0 36 24" aria-label="Play video">
  <rect width="36" height="24" rx="6" fill="#fff"/>
  <path d="M14 7L23 12L14 17Z" fill="#333"/>
</svg>

<h2 class="section-title" style="top:2988px">Frequently Asked Questions</h2>
<div class="faq-item" style="top:3084px">Sed ut perspiciatis unde omnis iste natus error sit voluptatem<span class="plus"></span></div>
<div class="faq-item" style="top:3166px">Sed ut perspiciatis unde omnis iste natus error sit voluptatem<span class="plus"></span></div>
<div class="faq-item" style="top:3248px">Sed ut perspiciatis unde omnis iste natus error sit voluptatem<span class="plus"></span></div>
<div class="faq-item" style="top:3328px">Sed ut perspiciatis unde omnis iste natus error sit voluptatem<span class="plus"></span></div>
<div class="faq-item" style="top:3408px">Sed ut perspiciatis unde omnis iste natus error sit voluptatem<span class="plus"></span></div>
<div class="faq-item" style="top:3486px">Sed ut perspiciatis unde omnis iste natus error sit voluptatem<span class="plus"></span></div>

<svg class="abs" style="left:0;top:3620px" width="1200" height="362" viewBox="0 0 1200 362">
  <path d="M0 25C180 -5 380 60 600 40C820 20 1000 -10 1200 20V362H0Z" fill="var(--blush)"/>
  <path d="M0 18C180 -12 380 53 600 33C820 13 1000 -17 1200 13V20C1000 -10 820 20 600 40C380 60 180 -5 0 25Z" fill="var(--wave)"/>
</svg>
<div class="abs logo" style="left:0;width:1200px;text-align:center;top:3738px">Virela Hair Extensions</div>
<nav class="footer-nav">
  <a href="#" style="left:343px">HOME</a>
  <a href="#" style="left:431px">ABOUT</a>
  <a href="#" style="left:518px">SHOP</a>
  <a href="#" style="left:636px">HOW IT WORKS</a>
  <a href="#" style="left:748px">FAQ</a>
  <a href="#" style="left:840px">CONTACT</a>
</nav>
<a class="social" href="#" aria-label="Photo sharing profile" style="left:525px"></a>
<a class="social" href="#" aria-label="Social network page" style="left:578px"></a>
<a class="social" href="#" aria-label="Microblog profile" style="left:632px"></a>
<div class="abs copyright">@2023 COPYRIGHTS.&nbsp; VIRELA HAIR EXTENSIONS.ALL RIGHTS RESERVED.</div>

</body>
</html>
```